Birchline Septic Solutions

Would like to see some single sided ones but would also like to see some double sided with one sided only being the logo. Owners name is Colin Vandro. Phone number is 555-214-0387
Services are pumping, inspections, installs, and repairs

Contact Information for Business Card

555-241-0387 Colin Vandro Ashford Falls, OH

```html
<!DOCTYPE html>
<html lang="en">
<head>
<meta charset="utf-8">
<title>Birchline Septic Solutions – Business Cards</title>
<link href="https://fonts.googleapis.com/css2?family=Open+Sans:wght@400;600;700&display=swap" rel="stylesheet">
<style>
  :root {
    --stage: #222224;
    --card: #212125;
    --teal: #22bdb6;
    --white: #ffffff;
    --soft: #e9e9ea;
  }
  * { box-sizing: border-box; margin: 0; padding: 0; }
  html, body {
    width: 1200px; height: 779px; overflow: hidden;
    background: var(--stage);
    font-family: "Open Sans", Arial, sans-serif;
  }
  .stage {
    position: relative; width: 1200px; height: 779px;
  }
  .card {
    position: absolute; top: 235px;
    width: 540px; height: 309px;
    background: var(--card);
    border-radius: 26px;
    border-bottom: 4px solid var(--teal);
    border-left: 2px solid var(--teal);
    box-shadow: 0 18px 40px rgba(0,0,0,.55);
    overflow: hidden;
  }
  .card--front { left: 40px; }
  .card--back { left: 620px; }

  .wordmark {
    display: flex; align-items: center; gap: 14px;
    color: var(--white); font-weight: 700;
  }
  .wordmark__square {
    width: 18px; height: 18px; background: var(--teal); flex: none;
  }
  .wordmark__text { line-height: 1; }
  .wordmark__name { display: block; text-transform: uppercase; letter-spacing: 2px; }
  .wordmark__tag { display: block; text-transform: uppercase; letter-spacing: 6px; margin-top: 8px; }

  .card--front .wordmark {
    position: absolute; left: 50%; top: 50%; transform: translate(-50%, -50%);
  }
  .card--front .wordmark__name { font-size: 50px; }
  .card--front .wordmark__tag { font-size: 17px; }

  .card--back .wordmark { position: absolute; left: 36px; top: 110px; gap: 10px; }
  .card--back .wordmark__square { width: 13px; height: 13px; }
  .card--back .wordmark__name { font-size: 32px; }
  .card--back .wordmark__tag { font-size: 11px; letter-spacing: 4px; margin-top: 6px; }

  .contact {
    position: absolute; right: 48px; top: 28px; text-align: right;
    color: var(--soft);
  }
  .contact__name { font-size: 26px; font-weight: 700; color: var(--white); line-height: 1.1; }
  .contact__first { color: var(--teal); }
  .contact__line { font-size: 13px; font-weight: 400; margin-top: 3px; display: flex; justify-content: flex-end; align-items: center; gap: 6px; }
  .contact__icon { width: 12px; height: 12px; }
  .accent-bar {
    position: absolute; right: 18px; top: 0; width: 14px; height: 82px;
    background: var(--teal);
  }

  .services { position: absolute; left: 40px; bottom: 28px; color: var(--white); }
  .services__title { font-size: 15px; font-weight: 600; color: var(--teal); text-transform: uppercase; margin-bottom: 3px; }
  .services__list { list-style: none; }
  .services__item { font-size: 14px; line-height: 1.45; display: flex; align-items: center; gap: 8px; padding-left: 6px; }
  .services__item::before {
    content: ""; width: 8px; height: 8px; border-radius: 50%; background: var(--teal);
  }
</style>
</head>
<body>
<main class="stage">
  <section class="card card--front" aria-label="Card front">
    <div class="wordmark">
      <span class="wordmark__square"></span>
      <span class="wordmark__text">
        <span class="wordmark__name">Birchline</span>
        <span class="wordmark__tag">Septic Solutions</span>
      </span>
    </div>
  </section>

  <section class="card card--back" aria-label="Card back">
    <span class="accent-bar"></span>
    <div class="contact">
      <p class="contact__name"><span class="contact__first">Colin</span> Vandro</p>
      <p class="contact__line">Ashford Falls, OH
        <svg class="contact__icon" viewBox="0 0 24 24" aria-hidden="true"><path fill="#22bdb6" d="M6.6 10.8a15.1 15.1 0 0 0 6.6 6.6l2.2-2.2a1 1 0 0 1 1-.25 11.4 11.4 0 0 0 3.6.57 1 1 0 0 1 1 1V20a1 1 0 0 1-1 1A17 17 0 0 1 3 4a1 1 0 0 1 1-1h3.5a1 1 0 0 1 1 1c0 1.25.2 2.45.57 3.57a1 1 0 0 1-.25 1z"/></svg>
      </p>
      <p class="contact__line">555-241-0387</p>
    </div>

    <div class="wordmark">
      <span class="wordmark__square"></span>
      <span class="wordmark__text">
        <span class="wordmark__name">Birchline</span>
        <span class="wordmark__tag">Septic Solutions</span>
      </span>
    </div>

    <div class="services">
      <p class="services__title">Services</p>
      <ul class="services__list">
        <li class="services__item">Pumping</li>
        <li class="services__item">Inspections</li>
        <li class="services__item">Installs</li>
        <li class="services__item">And Repairs</li>
      </ul>
    </div>
  </section>
</main>
</body>
</html>
```